Local massage therapist needs some new marketing material

Hi there! I am a massage therapist here in Denver, CO in Alder Bend(shopping and art district) of the city. My business is called Lumo Bodywork of Denver. My practice has an eastern influence and I do reflexology, thai massage and use Chinese herbs, etc. I know all my clients and pay close attention to details. I am also very respectful of tradition and it shows in how I work. I tend to like modern, clean, fun, Asian designs. I am wanting a new business card and brochure. I have a logo and branding for my business that I want used in the design. Currently, the sign for my building is purple and I think my logo was designed to be purple. I will attach pictures of it and can send whatever files are necessary so it can be integrated into the brochure, etc. I like the purple but open to using other colors as well. Thanks!
My website is lumobodyworkofdenver.example where info can be gathered about me and services/fees for brochure.
Updates

Just increased budget. Please see new feedback in discussion thread.

Thanks!

                                       HEY ALL,

Just wanted to let you know that I made a change to my website. It is on the Prices Page. I no longer have the frequent  flyer prices but I added discounts. Let me know if you have any questions. Thanks so much!

Target Market(s)

healthy, urban, educated, upper middle class, yogis

Industry/Entity Type

Marketing

Requirements
Must have
• logo stays purple
Should not have
• not too busy

```html
<!DOCTYPE html>
<html lang="en">
<head>
<meta charset="utf-8">
<title>Lumo Bodywork of Denver – Business Card</title>
<link rel="stylesheet" href="https://fonts.googleapis.com/css2?family=Open+Sans:ital,wght@0,400;0,600;0,700;1,400&display=swap">
<style>
  :root {
    --purple: #5b2a86;
    --purple-soft: #e7dcf1;
    --ink: #555555;
    --ink-light: #777777;
    --rule: #9a9a9a;
    --card: #ffffff;
    --backdrop: #ecebe8;
  }
  * { margin: 0; padding: 0; box-sizing: border-box; }
  html, body {
    width: 1200px; height: 720px; overflow: hidden;
    background: var(--backdrop);
    font-family: "Open Sans", Arial, sans-serif;
    color: var(--ink);
  }
  .stage {
    width: 1200px; height: 720px;
    display: flex; align-items: center; justify-content: center; gap: 48px;
  }
  .card {
    position: relative;
    width: 540px; height: 309px;
    background: var(--card);
    box-shadow: 0 2px 10px rgba(0,0,0,.12);
    overflow: hidden;
  }
  .wordmark {
    color: var(--purple);
    font-weight: 400;
    letter-spacing: .12em;
    line-height: 1;
  }
  .ornament {
    position: absolute;
    background: var(--purple-soft);
    border-radius: 50%;
  }

  /* Front */
  .card-front .wordmark { position: absolute; left: 40px; top: 48px; font-size: 50px; }
  .card-front .ornament { right: 44px; top: 24px; width: 170px; height: 170px; }
  .contact { position: absolute; left: 40px; top: 150px; }
  .contact-name { color: var(--purple); font-weight: 700; font-size: 16px; }
  .contact-title { font-size: 11px; color: var(--ink-light); margin-bottom: 8px; }
  .contact-list { list-style: none; font-size: 12.5px; line-height: 22px; }
  .contact-list li { display: flex; align-items: center; gap: 7px; }
  .contact-list svg { width: 13px; height: 13px; flex: none; }
  .contact-address { padding-left: 20px; margin-top: 4px; }

  /* Back */
  .card-back .ornament { right: 50px; top: 18px; width: 64px; height: 64px; }
  .card-back .wordmark { position: absolute; right: 38px; top: 92px; font-size: 38px; }
  .appointment { position: absolute; left: 36px; top: 140px; right: 36px; font-size: 13px; }
  .appointment-heading {
    color: var(--purple); font-weight: 700; font-size: 13px;
    display: flex; align-items: flex-end; gap: 8px; margin-bottom: 14px;
  }
  .appointment-heading::after { content: ""; flex: 1; border-bottom: 1px solid var(--rule); margin-bottom: 3px; }
  .field-row { display: flex; align-items: flex-end; gap: 6px; margin-bottom: 12px; }
  .blank { display: inline-block; border-bottom: 1px solid var(--rule); height: 14px; }
  .blank-name { width: 130px; }
  .blank-time { width: 110px; }
  .blank-date { width: 250px; }
  .hours { line-height: 19px; margin-top: 4px; }
  .cancel-note { font-style: italic; color: var(--ink-light); margin-top: 10px; }
</style>
</head>
<body>
<main class="stage">

  <section class="card card-front">
    <div class="wordmark">LUMO</div>
    <div class="ornament" role="img" aria-label="Brand ornament area"></div>
    <div class="contact">
      <p class="contact-name">Your Name</p>
      <p class="contact-title">Title</p>
      <ul class="contact-list">
        <li>
          <svg viewBox="0 0 16 16" aria-hidden="true"><circle cx="8" cy="8" r="8" fill="#5b2a86"/><path d="M5.4 4.2l1.3 1.9-.8.9c.5 1.2 1.4 2.1 2.6 2.6l.9-.8 1.9 1.3-.7 1.4c-3 0-6.2-3.2-6.2-6.2z" fill="#fff"/></svg>
          303.555.0142
        </li>
        <li>
          <svg viewBox="0 0 16 16" aria-hidden="true"><circle cx="8" cy="8" r="8" fill="#5b2a86"/><rect x="4" y="5.2" width="8" height="5.6" fill="#fff"/><path d="M4 5.4l4 3 4-3" stroke="#5b2a86" stroke-width=".9" fill="none"/></svg>
          info@lumobodyworkofdenver.example
        </li>
        <li>
          <svg viewBox="0 0 16 16" aria-hidden="true"><circle cx="8" cy="8" r="8" fill="#5b2a86"/><g stroke="#fff" stroke-width=".9" fill="none"><circle cx="8" cy="8" r="4"/><ellipse cx="8" cy="8" rx="1.8" ry="4"/><path d="M4 8h8"/></g></svg>
          www.lumobodyworkofdenver.example
        </li>
      </ul>
      <p class="contact-list contact-address">1180 E Linden Ave, Alder Bend, CO 80999</p>
    </div>
  </section>

  <section class="card card-back">
    <div class="ornament" role="img" aria-label="Brand ornament area"></div>
    <div class="wordmark">LUMO</div>
    <div class="appointment">
      <p class="appointment-heading">YOUR APPOINTMENT</p>
      <p class="field-row">Name : <span class="blank blank-name"></span> Time : <span class="blank blank-time"></span>am / pm</p>
      <p class="field-row">Date : <span class="blank blank-date"></span></p>
      <p class="hours">Tues - Fri 9am - 7pm Sat 9am-4pm<br>(Appointments required) No walk-ins please.</p>
      <p class="cancel-note">We appreciate a 24 hr. notice for cancellations</p>
    </div>
  </section>

</main>
</body>
</html>
```